Business cards to launch an education platform

Hi,
I am looking at having new business cards designed.
I am a startup, developing a web platform for schools and university, the education world. It's an online assessment system.
I would like a card that looks classy, and that is using the colors and the font of my logo.

I have attached:
1) my logo
2) A business card that I have designed quickly so you can have all the information required in the card, but I really don't like it.
3) The font that I am using (Lato Regular) to design my web platform
4) Some screenshots of my web platform so you can have a look at the style that I have.

Target Market(s)

Major market: Education system: Schools and university
Minor markets: Business in general

Industry/Entity Type

Business

Contact Information for Business Card

Clara Fenwick
Director

M: 0437 518 902
E: clara.fenwick@amberLoomSystems.com.au

Requirements
Must have
• The colors of my logo

```html
<!DOCTYPE html>
<html lang="en">
<head>
<meta charset="utf-8">
<title>Amber Loom Systems – Business Card</title>
<link rel="stylesheet" href="https://fonts.googleapis.com/css2?family=Lato:wght@400;700&display=swap">
<style>
  :root {
    --page-bg: #eceff2;
    --sky-blue: #22b6e4;
    --sky-light: #17dcf3;
    --sky-mid: #1fc4ec;
    --navy: #1b4f93;
    --brand-blue: #1f7fd0;
    --ink: #1d1d1f;
    --paper: #ffffff;
    --frame-line: rgba(255, 255, 255, 0.35);
  }

  * { box-sizing: border-box; margin: 0; padding: 0; }

  html, body {
    width: 1200px;
    height: 900px;
    overflow: hidden;
  }

  body {
    position: relative;
    background: var(--page-bg);
    font-family: "Lato", sans-serif;
  }

  .card {
    position: absolute;
    width: 560px;
    height: 320px;
    border-radius: 3px;
    box-shadow: 0 6px 18px rgba(0, 0, 0, 0.12);
    overflow: hidden;
  }

  /* Front */
  .card-front {
    left: 120px;
    top: 90px;
    background: var(--sky-blue);
  }

  .front-panel {
    position: absolute;
    inset: 22px;
    border: 1px solid var(--frame-line);
    background: radial-gradient(ellipse at 50% 50%, var(--sky-light) 0%, var(--sky-mid) 45%, var(--sky-blue) 100%);
    display: flex;
    align-items: center;
    justify-content: center;
  }

  .front-wordmark {
    color: var(--paper);
    font-weight: 400;
    text-align: center;
    line-height: 1.15;
  }

  .front-wordmark .line-main {
    display: block;
    font-size: 32px;
    letter-spacing: 4px;
    text-transform: uppercase;
  }

  .front-wordmark .line-sub {
    display: block;
    font-size: 22px;
    letter-spacing: 3px;
  }

  /* Back */
  .card-back {
    left: 520px;
    top: 490px;
    background: var(--paper);
  }

  .contact-person {
    position: absolute;
    left: 250px;
    top: 48px;
  }

  .person-name {
    color: var(--navy);
    font-weight: 700;
    font-size: 20px;
  }

  .person-role {
    color: var(--ink);
    font-size: 14px;
    margin-left: 8px;
  }

  .contact-list {
    position: absolute;
    left: 268px;
    top: 118px;
    list-style: none;
    font-size: 14px;
    color: var(--ink);
  }

  .contact-list li {
    display: flex;
    align-items: center;
    gap: 8px;
    margin-bottom: 10px;
  }

  .contact-icon {
    width: 12px;
    height: 12px;
    flex: none;
  }

  .brand-lockup {
    position: absolute;
    left: 40px;
    bottom: 44px;
    display: flex;
    align-items: center;
    gap: 16px;
  }

  .brand-mark {
    width: 52px;
    height: 52px;
    background: var(--brand-blue);
  }

  .brand-name {
    color: var(--navy);
    font-weight: 400;
    font-size: 28px;
    letter-spacing: 2px;
    line-height: 1.05;
  }
</style>
</head>
<body>

  <section class="card card-front" aria-label="Card front">
    <div class="front-panel" role="img" aria-label="Soft blue field where a faint repeating brand pattern belongs">
      <p class="front-wordmark">
        <span class="line-main">Amber Loom</span>
        <span class="line-sub">Systems</span>
      </p>
    </div>
  </section>

  <section class="card card-back" aria-label="Card back">
    <div class="contact-person">
      <p class="person-name">Clara Fenwick</p>
      <p class="person-role">Director</p>
    </div>

    <ul class="contact-list">
      <li>
        <svg class="contact-icon" viewBox="0 0 24 24" aria-hidden="true">
          <path fill="#1b4f93" d="M6.6 10.8a15.1 15.1 0 0 0 6.6 6.6l2.2-2.2c.3-.3.7-.4 1-.2 1.1.4 2.3.6 3.6.6.6 0 1 .4 1 1V20c0 .6-.4 1-1 1A17 17 0 0 1 3 4c0-.6.4-1 1-1h3.5c.6 0 1 .4 1 1 0 1.3.2 2.5.6 3.6.1.3 0 .7-.2 1z"/>
        </svg>
        <span>0437 518 902</span>
      </li>
      <li>
        <svg class="contact-icon" viewBox="0 0 24 24" aria-hidden="true">
          <rect x="2" y="5" width="20" height="14" fill="#1b4f93"/>
          <path d="M2 5l10 8 10-8" fill="none" stroke="#ffffff" stroke-width="2"/>
        </svg>
        <span>clara.fenwick@amberLoomSystems.com.au</span>
      </li>
    </ul>

    <div class="brand-lockup">
      <div class="brand-mark" aria-hidden="true"></div>
      <p class="brand-name">Amber Loom<br>Systems</p>
    </div>
  </section>

</body>
</html>
```